Lotstallmart.com Webpage Design

Design Brief for lotstallmart.com (Copy of Brief also in attached Word file)

Name of Website- lotstallmart.com (existing logo and look & feel of website to be changed)

Logo - Finalised. The logo files are attached with the brief as “logo.jpeg”. The “Blue- Grey” version of the logo is for use on lighter backgrounds and the “Orange-White” version of the logo is for use on darker backgrounds. (A full Black version of the logo is also attached). Both versions may be used in different parts of the website. All attached files are in .png format.
Status - The website in functional and is undergoing user trials. However, we want to improve the look & feel of the website so at it seems
a. cotemporary,
b. Easy to Navigate
c. professional and
d. Vibrant.

Please visit ‘lotstallmart.com’ to check out the website and its functionalities – please use it only as a reference for the features & functions to be provided, however the designer should use a ‘Free Hand’ in designing the composition of various parts of the webpage without getting too influenced by the existing design

Objective of the Website ‘lotstallmart.com –
a. It is a portal focussed on listing of ‘Retail’ specific real-estate properties by developers, owners and realty brokers. The properties shall listed under the following four categories-
i. Retail Malls
ii. Shopping Complexes
iii. High-street shops
iv. Retail Warehouses
*refer lotstallmart.com for better clarity

b. The abovementioned properties shall be listed either for ‘Sale’ or ‘rent\lease’ or both

c. Users shall visit the site in case they wish to acquire a retail \ shop space either on ‘sale’ or ‘rent’. These Users would be able to specify the ‘Search Criteria’ through the tool-bars provided on the website – the ‘Search Criteria’ shall comprise of ‘Type of space category’, ‘City’, ‘Locality’, transaction type ie ‘Rent \ Sale’ and ‘Area Range’

d. The main revenue model for the website shall be listing fee ( or advertising charges ) payable by those listing their properties on the website.

Three Main Pages of Website (lotstallmart.com) that need to be designed -
a. Main Home Page (visit the web link - http://lotstallmart.com/ ) - The main home page has the “Search Toolbar” for specifying of Search Criteria by the User. It shall also have the following features & functions-
i. Main Advertising Banner
ii. Featured Projects
iii. New Launches
iv. Toolbar with buttons – ‘Advertise with Us’, ‘Listings Alert’, ‘Mart Wizards’, ‘Advertiser Login’

b. Property Listings Page (visit the web link - http://lotstallmart.com/gurgaon-in-india ) - The List of property options that match the Criteria specified by the ‘User’ get displayed on this page.

c. Property Detail Page - When the ‘User’ clicks on the “More….” Button on the ‘Property Listings Page’ (given in point b. above) the web page with the details of the property opens. (For Example – visit the web link - http://lotstallmart.com/vorne-Shopping-Complex-vorne-quadrion-gurgaon-636 )

Note:- Please refer to attached ‘Shopping’ related images the designer may use them on the website to provide a look & feel of retail if required – either separately or rotate in a single window

Target Market(s)

Retailers & Investors looking for retail space, Real Estate Brokers, Developers

Industry/Entity Type

Advertising

Number of Pages Required

3 page

Requirements
Must have
• Refer to existing site lotstallmart.com -- all the existing functionalities are a must have.
Nice to have
• The Designer may use the retail related images on the website if required for making it more vibrant. Refer attached images Shopping(1-6).jpg

```html
<!DOCTYPE html>
<html lang="en">
<head>
<meta charset="utf-8">
<title>Lotstallmart.com – Retail Space Portal</title>
<link href="https://fonts.googleapis.com/css2?family=Questrial&family=Arimo:ital,wght@0,400;0,700;1,400;1,700&family=Tinos:ital@1&display=swap" rel="stylesheet">
<style>
:root{
  --blue:#0aa0ee;
  --blue-dark:#0b7fd0;
  --ink:#222;
  --muted:#555;
  --dark:#2b2b2b;
  --panel:#3a3a3a;
  --line:#c9c9c9;
  --paper:#f2f2f2;
  --white:#fff;
}
*{box-sizing:border-box;margin:0;padding:0}
html,body{width:692px;height:1200px;overflow:hidden}
body{position:relative;background:var(--white);font-family:Arimo,Arial,sans-serif;color:var(--ink)}
.abs{position:absolute}
.topbar{left:0;top:0;width:692px;height:26px;background:#1f1f1f}
.lang{left:360px;top:8px;color:#fff;font-size:7px}
.flag{top:6px;width:20px;height:13px}
.account{left:545px;top:0;width:90px;height:20px;background:var(--blue);border-radius:0 0 4px 4px;color:#fff;font-size:8px;text-align:center;line-height:20px}
.hero-zone{left:0;top:26px;width:692px;height:335px;background:#ebebeb}
.brand{left:62px;top:44px;display:flex;align-items:center;gap:6px}
.brand-dot{width:18px;height:18px;border-radius:50%;background:var(--blue)}
.brand-name{font-family:Questrial,sans-serif;font-size:22px;color:var(--blue)}
.list-prop{left:471px;top:37px;font-size:7.5px;color:#333}
.adv-login{left:555px;top:33px;width:72px;height:17px;background:var(--blue);border:1px solid #7fd0ff;border-radius:3px;color:#fff;font-size:7.5px;font-weight:700;text-align:center;line-height:15px}
.adv-reg{left:541px;top:55px;font-size:7.5px;font-style:italic;color:var(--blue)}
.nav{left:353px;top:94px;display:flex;font-family:Questrial,sans-serif;font-size:9px;color:#333}
.nav span{padding:0 12px;height:18px;line-height:18px}
.nav .on{background:var(--blue);color:#fff}
.search{left:64px;top:120px;width:174px;height:223px;background:#e3e3e3;border:1px solid #bdbdbd;border-radius:3px}
.search-tab{left:14px;top:-2px;width:150px;height:24px;background:linear-gradient(#1d8ee0,#0c62b5);border-radius:3px 3px 0 0;color:#fff;font-style:italic;font-weight:700;font-size:11.5px;text-align:center;line-height:24px}
.field-label{font-size:7px;font-style:italic;color:#333;left:19px}
.select{height:16px;background:#fff;border:1px solid #c4c4c4;border-radius:2px}
.select::after{content:"";position:absolute;right:0;top:1px;width:12px;height:12px;border-left:1px solid #ddd;background:linear-gradient(135deg,transparent 45%,#777 46%,#777 54%,transparent 55%)}
.find-btn{left:33px;top:183px;width:115px;height:24px;background:linear-gradient(#333,#000);border-radius:3px;color:#fff;font-size:8px;font-weight:700;font-style:italic;text-align:center;line-height:24px}
.slider{left:262px;top:120px;width:369px;height:224px;background:#d9d9d9;border:1px solid #bbb;border-radius:2px}
.slide-photo{left:5px;top:4px;width:358px;height:163px;background:linear-gradient(180deg,#a9c6dd 0%,#b56a55 40%,#8a4b3a 70%,#6f7b55 100%)}
.caption{left:5px;top:128px;width:358px;height:39px;background:rgba(0,0,0,.55);color:#fff;font-size:8px;font-weight:700;padding:6px 4px;line-height:13px}
.thumb{top:177px;width:50px;height:35px;border:1px solid #fff;background:linear-gradient(#cfc3b0,#8f7a60)}
.arrow{top:186px;width:16px;height:16px}
.band{left:0;top:361px;width:692px;height:63px;background:var(--blue)}
.band-item{top:18px;color:#fff;font-family:Questrial,sans-serif;font-size:12px;line-height:14px}
.band-sep{top:6px;width:1px;height:51px;background:rgba(255,255,255,.35)}
.featured-title{left:58px;top:443px;font-family:Questrial,sans-serif;font-size:20px;color:#222}
.featured-title small{font-size:8px;color:var(--blue);margin-left:4px}
.grid{left:58px;top:477px;width:578px;height:439px;border:1px solid #bbb}
.card{width:130px;height:193px;border:1px solid #ccc;border-radius:4px;background:#fff}
.card-photo{left:9px;top:6px;width:110px;height:70px;border:2px solid #ddd;background:linear-gradient(90deg,#6d5a45,#cdbfae 55%,#f1ece6)}
.price{left:33px;top:68px;width:60px;height:13px;background:var(--blue);color:#fff;font-size:8.5px;font-weight:700;text-align:center;line-height:13px;border-radius:2px}
.city{left:0;top:88px;width:130px;text-align:center;font-family:Questrial,sans-serif;font-size:14px;font-weight:700}
.blurb{left:7px;top:110px;width:114px;font-size:7px;line-height:11.6px;color:#444;text-align:justify}
.view-btn{width:82px;height:18px;border:1px solid #bbb;border-radius:3px;background:linear-gradient(#fff,#e6e6e6);font-size:7.5px;text-align:center;line-height:16px;color:#111}
.pager-label{left:490px;top:942px;font-family:Tinos,serif;font-style:italic;font-size:11px;color:#777}
.page{top:935px;width:26px;height:25px;border:1px solid #aaa;border-radius:3px;background:linear-gradient(#eee,#ccc);font-family:Tinos,serif;font-style:italic;font-size:12px;text-align:center;line-height:23px}
.page.on{background:linear-gradient(#2a95e8,#0c62b5);color:#fff;border-color:#0c62b5}
.footer{left:0;top:980px;width:692px;height:165px;background:var(--blue)}
.foot-h{font-family:Questrial,sans-serif;font-weight:700;font-size:13px;color:#fff}
.foot-p{font-size:7px;color:#fff;line-height:11.6px}
.input{height:17px;background:#fff;font-size:6.5px;color:#999;padding:4px}
.divider{top:12px;width:1px;height:140px;background:rgba(255,255,255,.45)}
.wizards{left:455px;top:991px;width:170px;height:137px;background:var(--panel);border-radius:3px}
.dark-btn{height:20px;background:#111;border:1px solid #888;border-radius:3px;color:#fff;font-weight:700;font-size:10px;text-align:center;line-height:18px}
.base{left:0;top:1145px;width:692px;height:55px;background:var(--dark)}
.base-links{left:57px;top:1155px;font-size:6.8px;color:#fff;font-weight:700}
.base-copy{left:60px;font-size:7px;color:#ccc}
.base-brand{left:487px;top:1160px;display:flex;align-items:center;gap:5px}
.base-brand .brand-name{color:#fff;font-size:17px}
</style>
</head>
<body>

<div class="abs topbar"></div>
<div class="abs lang">Select Language:</div>
<div class="abs flag" style="left:421px;background:linear-gradient(#c60b1e 25%,#ffc400 25% 75%,#c60b1e 75%)"></div>
<div class="abs flag" style="left:449px;background:#fff;border:1px solid #ddd"></div>
<div class="abs flag" style="left:476px;background:#009c3b"></div>
<div class="abs flag" style="left:503px;background:#de2910"></div>
<div class="abs account">Register &nbsp; | &nbsp; Login</div>

<div class="abs hero-zone"></div>
<div class="abs brand"><span class="brand-dot"></span><span class="brand-name">lotstallmart</span></div>
<div class="abs list-prop">List Your Property Here</div>
<div class="abs adv-login">Advertiser Login</div>
<div class="abs adv-reg">New Advertiser - Register</div>
<nav class="abs nav"><span class="on">Home</span><span>Advertise with us</span><span>Mart Wizards</span><span>Listing Alert</span></nav>

<form class="abs search">
  <div class="abs search-tab">Quick Property Search</div>
  <div class="abs field-label" style="top:34px">Select Area</div>
  <div class="abs select" style="left:19px;top:45px;width:143px"></div>
  <div class="abs field-label" style="top:69px">Property Types</div>
  <div class="abs select" style="left:19px;top:80px;width:143px"></div>
  <div class="abs field-label" style="top:104px">Price Range</div>
  <div class="abs select" style="left:19px;top:117px;width:66px"></div>
  <div class="abs select" style="left:96px;top:117px;width:66px"></div>
  <div class="abs field-label" style="top:144px">Bedroom(s)</div>
  <div class="abs select" style="left:19px;top:156px;width:143px"></div>
  <div class="abs find-btn">FIND PROPERTY</div>
</form>

<div class="abs slider">
  <div class="abs slide-photo" role="img" aria-label="Photo of a red-brick family house under a blue sky"></div>
  <div class="abs caption">4471 Harbor Lane<br>2 Family, 5 Bedroom, 4 Bathroom</div>
  <svg class="abs arrow" style="left:9px" viewBox="0 0 16 16"><circle cx="8" cy="8" r="8" fill="#1c6fc4"/><path d="M10 4L6 8l4 4" stroke="#fff" stroke-width="2" fill="none"/></svg>
  <div class="abs thumb" role="img" aria-label="Living room thumbnail" style="left:33px"></div>
  <div class="abs thumb" role="img" aria-label="House and garden thumbnail" style="left:95px;background:linear-gradient(#b0775e,#4e8a3c)"></div>
  <div class="abs thumb" role="img" aria-label="Staircase thumbnail" style="left:157px;background:linear-gradient(#eee,#999)"></div>
  <div class="abs thumb" role="img" aria-label="Bedroom thumbnail" style="left:219px;background:linear-gradient(#d8c29a,#7d6040)"></div>
  <div class="abs thumb" role="img" aria-label="Lounge thumbnail" style="left:281px"></div>
  <svg class="abs arrow" style="left:345px" viewBox="0 0 16 16"><circle cx="8" cy="8" r="8" fill="#1c6fc4"/><path d="M6 4l4 4-4 4" stroke="#fff" stroke-width="2" fill="none"/></svg>
</div>

<section class="abs band">
  <svg class="abs" style="left:60px;top:16px" width="26" height="28" viewBox="0 0 26 28"><circle cx="11" cy="11" r="8" stroke="#fff" stroke-width="2.5" fill="none"/><path d="M17 17l7 8" stroke="#fff" stroke-width="3"/></svg>
  <div class="abs band-item" style="left:96px">Search over 16 Thousands<br>apartments and homes</div>
  <div class="abs band-sep" style="left:252px"></div>
  <svg class="abs" style="left:270px;top:20px" width="28" height="22" viewBox="0 0 28 22"><rect x="1" y="4" width="26" height="17" rx="3" stroke="#fff" stroke-width="2" fill="none"/><circle cx="14" cy="12.5" r="5" stroke="#fff" stroke-width="2" fill="none"/><rect x="4" y="1" width="6" height="3" fill="#fff"/></svg>
  <div class="abs band-item" style="left:304px">View property videos,<br>photos and Rent plans</div>
  <div class="abs band-sep" style="left:449px"></div>
  <div class="abs" style="left:470px;top:24px;width:10px;height:14px;background:#fff;opacity:.9"></div>
  <div class="abs band-item" style="left:490px">Share your favorites with<br>friends on social media</div>
</section>

<h2 class="abs featured-title">Featured Retail Projects<small>Across India</small></h2>

<div class="abs grid">
  <svg class="abs" style="left:0;top:0" width="578" height="439"><path d="M144 0V439M288 0V439M432 0V439M0 214H578" stroke="#bbb"/></svg>
</div>

<!-- row 1 -->
<article class="abs card" style="left:64px;top:481px"><div class="abs card-photo" role="img" aria-label="Dining room interior"></div><div class="abs price">$3,390</div><h3 class="abs city">Bhopal</h3><p class="abs blurb">Lorem Ipsum is simply dummy text of the printing and typesetting industry. Lorem Ipsum has been the industry's standard dummy text ever since the 1500s, when an unknown printer galley....</p></article>
<article class="abs card" style="left:210px;top:481px"><div class="abs card-photo" role="img" aria-label="Dining room interior"></div><div class="abs price">$2,489</div><h3 class="abs city">Noida</h3><p class="abs blurb">Lorem Ipsum is simply dummy text of the printing and typesetting industry. Lorem Ipsum has been the industry's standard dummy text ever since the 1500s, when an unknown printer galley....</p></article>
<article class="abs card" style="left:352px;top:481px"><div class="abs card-photo" role="img" aria-label="Dining room interior"></div><div class="abs price">$3,390</div><h3 class="abs city">Mohali</h3><p class="abs blurb">Lorem Ipsum is simply dummy text of the printing and typesetting industry. Lorem Ipsum has been the industry's standard dummy text ever since the 1500s, when an unknown printer galley....</p></article>
<article class="abs card" style="left:499px;top:481px"><div class="abs card-photo" role="img" aria-label="Dining room interior"></div><div class="abs price">$2,489</div><h3 class="abs city">Gurgaon</h3><p class="abs blurb">Lorem Ipsum is simply dummy text of the printing and typesetting industry. Lorem Ipsum has been the industry's standard dummy text ever since the 1500s, when an unknown printer galley....</p></article>
<a class="abs view-btn" style="left:88px;top:682px">VIEW THE LISTING</a>
<a class="abs view-btn" style="left:234px;top:682px">VIEW THE LISTING</a>
<a class="abs view-btn" style="left:376px;top:682px">VIEW THE LISTING</a>
<a class="abs view-btn" style="left:526px;top:682px">VIEW THE LISTING</a>

<!-- row 2 -->
<article class="abs card" style="left:64px;top:706px"><div class="abs card-photo" role="img" aria-label="Dining room interior"></div><div class="abs price">$3,390</div><h3 class="abs city">Bhopal</h3><p class="abs blurb">Lorem Ipsum is simply dummy text of the printing and typesetting industry. Lorem Ipsum has been the industry's standard dummy text ever since the 1500s, when an unknown printer galley....</p></article>
<article class="abs card" style="left:210px;top:706px"><div class="abs card-photo" role="img" aria-label="Dining room interior"></div><div class="abs price">$2,489</div><h3 class="abs city">Noida</h3><p class="abs blurb">Lorem Ipsum is simply dummy text of the printing and typesetting industry. Lorem Ipsum has been the industry's standard dummy text ever since the 1500s, when an unknown printer galley....</p></article>
<article class="abs card" style="left:352px;top:706px"><div class="abs card-photo" role="img" aria-label="Dining room interior"></div><div class="abs price">$3,390</div><h3 class="abs city">Mohali</h3><p class="abs blurb">Lorem Ipsum is simply dummy text of the printing and typesetting industry. Lorem Ipsum has been the industry's standard dummy text ever since the 1500s, when an unknown printer galley....</p></article>
<article class="abs card" style="left:499px;top:706px"><div class="abs card-photo" role="img" aria-label="Dining room interior"></div><div class="abs price">$2,489</div><h3 class="abs city">Gurgaon</h3><p class="abs blurb">Lorem Ipsum is simply dummy text of the printing and typesetting industry. Lorem Ipsum has been the industry's standard dummy text ever since the 1500s, when an unknown printer galley....</p></article>
<a class="abs view-btn" style="left:88px;top:907px">VIEW THE LISTING</a>
<a class="abs view-btn" style="left:234px;top:907px">VIEW THE LISTING</a>
<a class="abs view-btn" style="left:376px;top:907px">VIEW THE LISTING</a>
<a class="abs view-btn" style="left:526px;top:907px">VIEW THE LISTING</a>

<div class="abs pager-label">Page 1 of 3</div>
<div class="abs page on" style="left:554px">1</div>
<div class="abs page" style="left:582px">2</div>
<div class="abs page" style="left:610px">3</div>

<footer class="abs footer"></footer>
<h4 class="abs foot-h" style="left:60px;top:997px">Listing Alert</h4>
<svg class="abs" style="left:58px;top:1018px" width="36" height="34" viewBox="0 0 36 34"><path d="M2 14L18 2l16 12v19H2z" fill="#fff"/><path d="M2 14l16 11 16-11" stroke="#0aa0ee" stroke-width="1.5" fill="none"/><circle cx="18" cy="13" r="5" stroke="#0aa0ee" stroke-width="1.5" fill="none"/></svg>
<p class="abs foot-p" style="left:100px;top:1023px;width:100px">Suscribe &nbsp;for Fortnightly Email update on New Listings @ Lotstallmart</p>
<div class="abs input" style="left:59px;top:1063px;width:139px">Email Your Email Address:</div>
<div class="abs dark-btn" style="left:139px;top:1093px;width:59px">Subscribe</div>
<div class="abs divider" style="left:212px;top:992px"></div>
<h4 class="abs foot-h" style="left:230px;top:997px">Editor's Choice</h4>
<p class="abs foot-p" style="left:230px;top:1023px;width:195px">A "Select" Listing of Retail Properties Handpicked by our Editors based on their own positive evaluation on parameters &amp; attributes such as Design Concept, Location, Developer, Success Potential. So Read On to Check Out for yourself ............ ..</p>
<div class="abs divider" style="left:442px;top:992px"></div>
<div class="abs wizards">
  <h4 class="abs foot-h" style="left:11px;top:7px">Mart Wizards</h4>
  <div class="abs input" style="left:11px;top:34px;width:150px">Email Your Email Address:</div>
  <div class="abs input" style="left:11px;top:61px;width:150px;height:33px">Add Description of Requirement</div>
  <div class="abs dark-btn" style="left:103px;top:102px;width:58px">Send</div>
</div>

<div class="abs base"></div>
<div class="abs base-links">About Us &nbsp;| &nbsp;Privacy Policy &nbsp;| &nbsp;Terms of Use &nbsp;| &nbsp;Contact Us &nbsp;| &nbsp;Site Map &nbsp;| &nbsp;Retail Malls &nbsp;| &nbsp;Shopping Complex &nbsp;| &nbsp;High Street Shops &nbsp;| &nbsp;Retail Warehouses</div>
<div class="abs base-copy" style="top:1171px">Copyright © 2014 . lotstallmart All rights reserved.</div>
<div class="abs base-copy" style="top:1186px">website by Norvane Technologies.</div>
<div class="abs base-brand"><span class="brand-dot" style="background:#f5a623;width:14px;height:14px"></span><span class="brand-name">lotstallmart</span></div>

</body>
</html>
```